Moxy Fen needs some awesome stationary

Do you have what it takes to get my brand? You either do or you don't, have a crack at a design and you my just win my business.

I don't want to waste your or my time, so put your creative genius on either a business card or envelope.

I however need a package of stationary that follows the same brand. I will message you to complete the remaining should I like your first submission.

Here is what I need, have a go!

Basically I need the following for my small business based in melbourne.
- Letterhead (printer ready and MS Word)
- Business Card
- Compliments Slip
- Envelope
- Proposal Cover Page (MS Word only)
- Presentation Folder
- Marbled Fox Cards
- Student Name Tent
- Index Cards
- Vell-Ka

I am establishing the brand and it must be modern, professional but also relaxed; that is not formal and not corporate. It represents a company are leaders, but small enough to care and operate like a bunch of friends. We are bringing people and conversations back to business, and turfing out all the bureaucracy and crazy and wasteful procedures. Its about "lets talk and figure it out together and find even better ways".

Target Market(s)

Mainly companies that build software products, but Agile practices are used in many other industries (even graphic design projects)

Industry/Entity Type

Information Technology

Font styles to use
Sans Serif

Colors
3176b5
aaaaaa

Requirements
Must have
• I like curves and circles and not boxes or rectangles.
• I want a colour rich design with my brand colours, but it must be balanced.
• I want more modern than traditional, but simple modern
Should not have
• Not corporate
• Please don't waste my time if your not going to think about it.
• Don't mess with my primary logo
• Don't change my colours
• Don't overlay logo on image

```html
<!DOCTYPE html>
<html lang="en">
<head>
<meta charset="utf-8">
<title>Moxy Fen – Name Tent Cards</title>
<link href="https://fonts.googleapis.com/css2?family=Open+Sans:wght@600&display=swap" rel="stylesheet">
<style>
  :root {
    --backdrop: #3a9fd8;
    --brand-blue: #0d4f9b;
    --brand-grey: #8e9aab;
    --stripe-blue: #1a7fce;
    --stripe-grey: #b9b9bb;
    --fold: #a0a0a0;
    --paper: #ffffff;
  }
  * { box-sizing: border-box; margin: 0; padding: 0; }
  html, body {
    width: 1200px; height: 1200px; overflow: hidden;
    background: var(--backdrop);
    font-family: "Open Sans", Arial, sans-serif;
  }
  .canvas { position: relative; width: 1200px; height: 1200px; }

  .name-tent {
    position: absolute;
    background: var(--paper);
    box-shadow: 6px 7px 7px rgba(0, 0, 0, 0.3);
    display: flex; flex-direction: column;
  }
  .name-tent--striped { left: 42px; top: 82px; width: 1118px; height: 466px; }
  .name-tent--plain   { left: 45px; top: 620px; width: 1113px; height: 464px; }

  .tent-face { position: relative; flex: 1; }
  .tent-face--back { transform: rotate(180deg); }
  .tent-face--front { border-top: 1px solid var(--fold); }

  .brand-mark {
    position: absolute; left: 72px; top: 28px;
    width: 125px; height: 125px; border-radius: 50%;
    background: var(--brand-blue);
  }
  .brand-name {
    position: absolute; left: 61px; top: 160px;
    font-size: 38px; font-weight: 600; line-height: 1;
    color: var(--brand-blue); letter-spacing: 0.2px;
  }
  .edge-stripe {
    position: absolute; left: 0; bottom: 0;
    width: 100%; height: 13px; display: block;
  }
</style>
</head>
<body>
<div class="canvas">

  <div class="name-tent name-tent--striped">
    <div class="tent-face tent-face--back">
      <span class="brand-mark"></span>
      <span class="brand-name">Moxy Fen</span>
      <svg class="edge-stripe" viewBox="0 0 1118 13" preserveAspectRatio="none" aria-hidden="true">
        <defs>
          <linearGradient id="stripeGreyA" x1="0" y1="0" x2="0" y2="1">
            <stop offset="0" stop-color="#e6e6e8"/><stop offset="1" stop-color="#a9a9ab"/>
          </linearGradient>
          <linearGradient id="stripeBlueA" x1="0" y1="0" x2="0" y2="1">
            <stop offset="0" stop-color="#20a6ee"/><stop offset="1" stop-color="#0a5fb0"/>
          </linearGradient>
        </defs>
        <polygon points="0,0 224,0 214,13 0,13" fill="url(#stripeGreyA)"/>
        <polygon points="240,0 1118,0 1118,13 229,13" fill="url(#stripeBlueA)"/>
      </svg>
    </div>
    <div class="tent-face tent-face--front">
      <span class="brand-mark"></span>
      <span class="brand-name">Moxy Fen</span>
      <svg class="edge-stripe" viewBox="0 0 1118 13" preserveAspectRatio="none" aria-hidden="true">
        <polygon points="0,0 224,0 214,13 0,13" fill="url(#stripeGreyA)"/>
        <polygon points="240,0 1118,0 1118,13 229,13" fill="url(#stripeBlueA)"/>
      </svg>
    </div>
  </div>

  <div class="name-tent name-tent--plain">
    <div class="tent-face tent-face--back">
      <span class="brand-mark"></span>
      <span class="brand-name">Moxy Fen</span>
    </div>
    <div class="tent-face tent-face--front">
      <span class="brand-mark"></span>
      <span class="brand-name">Moxy Fen</span>
    </div>
  </div>

</div>
</body>
</html>
```